Unternehmen für Ordnung und Sauberkeit am Arbeitsplatz und Produkte zur Produktionsoptimierung benötigt Visitenkarten und Briefpapier
Zielgruppe
Produkte für Ordnung und Sauberkeit am Arbeitsplatz, Organisation von Arbeitsplätzen, Produkte zur Vereinfachung von Arbeitsabläufen, Produkte zur Produktionsoptimierung unter dem Lean Gedanke, Schlagwort: "5S", nachhaltig, sauber
Aufgabenstellung
Wir sind auf der Suche nach Visitenkarten und Briefpapier für das Unternehmen yourTidor. Nachhaltig, Sauber usw.. Unser Firmenlogo finden Sie anbei.

```html
<!DOCTYPE html>
<html lang="de">
<head>
<meta charset="utf-8">
<title>yourTidor – Briefpapier und Umschlag</title>
<link href="https://fonts.googleapis.com/css2?family=PT+Sans:wght@400;700&display=swap" rel="stylesheet">
<style>
  :root {
    --green: #23a532;
    --green-dark: #1a7d26;
    --grey: #858585;
    --text: #6a6a6a;
    --paper: #ffffff;
    --mark: #555555;
    --faint: #f6f6f6;
    --edge: #c8c8c8;
  }
  html, body { margin: 0; padding: 0; width: 1200px; height: 1000px; overflow: hidden; background: var(--paper); }
  svg.sheet { display: block; width: 1200px; height: 1000px; font-family: "PT Sans", sans-serif; }
  .crop { stroke: var(--mark); stroke-width: 0.7; }
  .crop-dash { stroke: var(--mark); stroke-width: 0.7; stroke-dasharray: 6 6; }
  .paper { fill: var(--paper); filter: url(#drop); }
  .band-grey { fill: var(--grey); }
  .band-green { fill: var(--green); }
  .brand { font-weight: 700; fill: var(--green); }
  .brand-grey { font-weight: 700; fill: var(--grey); }
  .brand-faint { font-weight: 700; fill: var(--faint); }
  .info { fill: var(--text); font-size: 6.2px; }
  .info-sm { fill: var(--text); font-size: 5.4px; }
  .rule { stroke: var(--text); stroke-width: 0.8; }
  .icon-box { fill: var(--green); }
  .icon-line { stroke: #fff; stroke-width: 0.9; fill: none; }
  .flap { fill: var(--paper); stroke: var(--edge); stroke-width: 0.8; }
  .window { fill: var(--paper); stroke: var(--edge); stroke-width: 1; }
  .recipient { fill: var(--text); font-size: 6px; }
</style>
</head>
<body>
<svg class="sheet" viewBox="0 0 1200 1000" xmlns="http://www.w3.org/2000/svg">
  <defs>
    <filter id="drop" x="-5%" y="-5%" width="110%" height="110%">
      <feDropShadow dx="2" dy="2" stdDeviation="2" flood-color="#000" flood-opacity="0.25"/>
    </filter>
  </defs>

  <!-- Letterhead -->
  <g class="letterhead">
    <g class="crop-marks">
      <line class="crop" x1="96" y1="165" x2="96" y2="190"/>
      <line class="crop" x1="516" y1="165" x2="516" y2="190"/>
      <line class="crop" x1="58" y1="202" x2="83" y2="202"/>
      <line class="crop" x1="529" y1="202" x2="555" y2="202"/>
      <line class="crop" x1="58" y1="797" x2="83" y2="797"/>
      <line class="crop" x1="529" y1="797" x2="555" y2="797"/>
      <line class="crop" x1="96" y1="809" x2="96" y2="835"/>
      <line class="crop" x1="516" y1="809" x2="516" y2="835"/>
      <line class="crop" x1="88" y1="406" x2="110" y2="406"/>
      <line class="crop" x1="88" y1="595" x2="110" y2="595"/>
    </g>
    <rect class="paper" x="96" y="202" width="420" height="595"/>
    <polygon class="band-grey" points="96,202 370,202 361,213 96,213"/>
    <polygon class="band-green" points="374,202 516,202 516,213 365,213"/>

    <g class="header-brand">
      <rect x="224" y="240" width="30" height="30" rx="4" fill="var(--green)"/>
      <text class="brand" x="262" y="268" font-size="36">yourTidor</text>
    </g>

    <text class="brand-faint" x="0" y="0" font-size="80" transform="translate(200 620) rotate(-55)">yourTidor</text>

    <g class="footer">
      <rect x="123" y="758" width="11" height="11" rx="2" fill="var(--green)"/>
      <text class="brand" x="137" y="768" font-size="12">yourTidor</text>
      <line class="rule" x1="189" y1="759" x2="189" y2="782"/>
      <text class="info-sm" x="199" y="765">Stadtbank Nordtal</text>
      <text class="info-sm" x="199" y="773">BLZ 100 200 30</text>
      <text class="info-sm" x="199" y="781">Kto 123456789</text>
      <line class="rule" x1="269" y1="759" x2="269" y2="782"/>
      <text class="info-sm" x="278" y="769">IBAN: DE00100200300123456789</text>
      <text class="info-sm" x="278" y="777">BIC: NORDDEXXXXX</text>
      <line class="rule" x1="398" y1="694" x2="398" y2="786"/>

      <rect class="icon-box" x="404" y="694" width="11" height="11" rx="2.5"/>
      <path d="M409.5 696.5a2.6 2.6 0 0 1 2.6 2.6c0 2-2.6 4.3-2.6 4.3s-2.6-2.3-2.6-4.3a2.6 2.6 0 0 1 2.6-2.6z" fill="#fff"/>
      <circle cx="409.5" cy="699.1" r="0.9" fill="var(--green)"/>
      <text class="brand" x="420" y="703" font-size="10">yourTidor</text>
      <text class="info" x="418" y="711">Ahornstraße 7</text>
      <text class="info" x="418" y="720">95100 Feldberg</text>

      <rect class="icon-box" x="404" y="726" width="11" height="10" rx="2.5"/>
      <path class="icon-line" d="M406.5 730c2-2 4-2 6 0M407.5 733.5h4v-2h-4z"/>
      <text class="info" x="417" y="733.5">04120 / 31847 2</text>

      <rect class="icon-box" x="404" y="739" width="11" height="10" rx="2.5"/>
      <rect class="icon-line" x="407" y="741" width="5" height="6"/>
      <text class="info" x="417" y="746">04120 / 31847 / 3 5</text>

      <rect class="icon-box" x="404" y="751" width="11" height="10" rx="2.5"/>
      <text x="409.5" y="758.6" font-size="8" fill="#fff" text-anchor="middle" font-weight="700">@</text>
      <text class="info" x="417" y="758.5">kontakt@yourtidor.de</text>

      <rect class="icon-box" x="404" y="764" width="11" height="10" rx="2.5"/>
      <circle class="icon-line" cx="409.5" cy="769" r="3"/>
      <path class="icon-line" d="M406.5 769h6M409.5 766v6"/>
      <text class="info" x="418" y="771.5">www.yourtidor.de</text>
    </g>

    <polygon class="band-green" points="96,786 370,786 361,797 96,797"/>
    <polygon class="band-grey" points="374,786 516,786 516,797 365,797"/>
  </g>

  <!-- Envelope front with open flap -->
  <g class="envelope-front">
    <g class="crop-marks">
      <line class="crop" x1="653" y1="216" x2="653" y2="241"/>
      <line class="crop" x1="1103" y1="216" x2="1103" y2="241"/>
      <line class="crop-dash" x1="615" y1="254" x2="640" y2="254"/>
      <line class="crop-dash" x1="1116" y1="254" x2="1142" y2="254"/>
      <line class="crop" x1="615" y1="485" x2="640" y2="485"/>
      <line class="crop" x1="1116" y1="485" x2="1142" y2="485"/>
      <line class="crop" x1="653" y1="497" x2="653" y2="523"/>
      <line class="crop" x1="1103" y1="497" x2="1103" y2="523"/>
    </g>
    <path class="flap" d="M653 254 L674 190 Q677 183 684 183 L1073 183 Q1080 183 1083 190 L1103 254 Z"/>
    <g class="flap-brand" transform="rotate(180 879 218)">
      <rect x="832" y="212" width="12" height="12" rx="2" fill="var(--grey)"/>
      <text class="brand-grey" x="848" y="225" font-size="20">yourTidor</text>
    </g>

    <rect class="paper" x="653" y="254" width="450" height="231"/>
    <line x1="653" y1="254.5" x2="1103" y2="254.5" stroke="var(--edge)" stroke-width="0.8"/>

    <g class="sender">
      <path d="M686 279.5a4.6 4.6 0 0 1 4.6 4.6c0 3.4-4.6 7-4.6 7s-4.6-3.6-4.6-7a4.6 4.6 0 0 1 4.6-4.6z" fill="none" stroke="var(--grey)" stroke-width="1.6"/>
      <circle cx="686" cy="284" r="1.5" fill="var(--grey)"/>
      <text class="brand" x="695" y="288" font-size="10">yourTidor</text>
      <text class="info-sm" x="695" y="296">Ahornstraße 7</text>
      <text class="info-sm" x="695" y="305">95100 Feldberg</text>
    </g>

    <rect class="window" x="681" y="384" width="180" height="72" rx="8"/>
    <g class="recipient-block">
      <text class="recipient" x="717" y="406">Marlene Berger</text>
      <text class="recipient" x="717" y="416">Am Lindenhof 18</text>
      <text class="recipient" x="717" y="425.5">41230 Talheim</text>
      <text class="recipient" x="717" y="435">SCHWEIZ</text>
    </g>

    <rect x="943" y="402" width="20" height="20" rx="3" fill="var(--green)"/>
    <text class="brand" x="968" y="423" font-size="27">yourTidor</text>

    <polygon class="band-grey" points="653,477 952,477 945,485 653,485"/>
    <polygon class="band-green" points="956,477 1103,477 1103,485 949,485"/>
  </g>

  <!-- Envelope back -->
  <g class="envelope-back">
    <g class="crop-marks">
      <line class="crop" x1="653" y1="527" x2="653" y2="553"/>
      <line class="crop" x1="1103" y1="527" x2="1103" y2="553"/>
      <line class="crop-dash" x1="615" y1="566" x2="640" y2="566"/>
      <line class="crop-dash" x1="1116" y1="566" x2="1142" y2="566"/>
      <line class="crop" x1="615" y1="797" x2="640" y2="797"/>
      <line class="crop" x1="1116" y1="797" x2="1142" y2="797"/>
      <line class="crop" x1="653" y1="809" x2="653" y2="835"/>
      <line class="crop" x1="1103" y1="809" x2="1103" y2="835"/>
    </g>
    <rect class="paper" x="653" y="566" width="450" height="231"/>
    <path class="flap" d="M653 566 L674 630 Q677 637 684 637 L1073 637 Q1080 637 1083 630 L1103 566 Z" filter="url(#drop)"/>
    <rect x="838" y="595" width="12" height="12" rx="2" fill="var(--grey)"/>
    <text class="brand-grey" x="854" y="607" font-size="20">yourTidor</text>
  </g>
</svg>
</body>
</html>
```